Corvane Paintless Dent Removal

Our company works on vehicles removing dents using a highly skilled trade which the metal is massaged out with special tools without disturbing the original paint, hence paintless dent removal. Besides keeping the paint and metal original its also very environmentally friendly since no paint or toxic fillers are used. Also we we are one of the most experienced companies in the business with 25 years

Target Market(s)

Retail Automobile consumers, Auto Dealerships and Auto Body Shops

Industry/Entity Type

Auto Repair

Contact Information for Business Card

Dale Hollister
PO Box 518 Brookmere, NY 11962
631-555-0148
corvanepdr@mailbox-example.com
website corvanepdr.example
youtube corvane paintless dent removal
25 years of experience removing Dents, Dings and Hail Damage

Font styles to use
Serif
Sans Serif

Colors

Designer to choose colors to be used in the design.

Requirements
Must have
• I do like things that are simple but classy and somewhat bold, also I like my logo so that should be somewhat important

```html
<!DOCTYPE html>
<html lang="en">
<head>
<meta charset="utf-8">
<title>Corvane Paintless Dent Removal — Business Card</title>
<link rel="stylesheet" href="https://fonts.googleapis.com/css2?family=Arimo:ital,wght@0,400;0,700;1,400&display=swap">
<style>
  :root {
    --navy: #0f2a4f;
    --green: #7cc516;
    --white: #ffffff;
    --paper: #f7f7f7;
    --ink: #1d1d1d;
    --rule: #9a9a9a;
    --backdrop: #e6e3de;
  }
  * { margin: 0; padding: 0; box-sizing: border-box; }
  html, body { width: 1200px; height: 900px; overflow: hidden; }
  body {
    background: var(--backdrop);
    font-family: "Arimo", Arial, sans-serif;
    position: relative;
  }
  .card {
    position: absolute;
    width: 476px;
    height: 294px;
    overflow: hidden;
    box-shadow: 0 4px 10px rgba(0,0,0,0.25);
  }
  /* Front */
  .card--front {
    left: 117px; top: 276px;
    background: linear-gradient(180deg, var(--white), var(--paper));
    border-radius: 0 40px 0 40px;
  }
  .front__brand {
    position: absolute;
    left: 0; right: 0; top: 72px;
    text-align: center;
    padding-left: 120px;
    font-weight: 700;
    font-size: 21px;
    color: var(--navy);
  }
  .front__name {
    position: absolute;
    left: 20px; top: 174px;
    display: flex; align-items: center;
    width: 432px;
    font-weight: 700; font-size: 17px;
    letter-spacing: 0.3px;
  }
  .front__name .first { color: var(--navy); margin-right: 5px; }
  .front__name .last { color: var(--green); }
  .front__name .rule { flex: 1; height: 1px; background: var(--rule); margin-left: 6px; }
  .contact-list {
    position: absolute; left: 22px; top: 206px;
    list-style: none; font-size: 14px; color: var(--ink);
  }
  .contact-list li { display: flex; align-items: center; height: 17.5px; }
  .contact-list svg { width: 10px; height: 10px; margin-right: 5px; fill: var(--green); }
  .front__address {
    position: absolute; right: 24px; top: 225px;
    text-align: right; font-size: 14px; line-height: 17.5px; color: var(--ink);
  }
  /* Back */
  .card--back {
    left: 623px; top: 277px;
    background: var(--navy);
    border-radius: 40px 0 40px 0;
  }
  .back__top {
    position: absolute; left: 0; top: 0; width: 100%; height: 122px;
    background: var(--green);
  }
  .back__tagline {
    position: absolute; left: 0; right: 0; top: 29px;
    text-align: center; font-style: italic; font-size: 12px;
    line-height: 15px; color: var(--white); letter-spacing: 0.3px;
  }
  .back__brand {
    position: absolute; left: 0; right: 0; top: 152px;
    text-align: center; font-weight: 700; font-size: 26px; color: var(--white);
  }
  .back__channel {
    position: absolute; left: 0; right: 0; top: 247px;
    display: flex; justify-content: center; align-items: center;
    font-size: 14px; color: var(--white);
  }
  .back__channel .marker {
    width: 18px; height: 18px; background: var(--white);
    border-radius: 3px; margin-right: 7px;
  }
</style>
</head>
<body>
  <section class="card card--front" aria-label="Business card front">
    <div class="front__brand">Corvane Paintless Dent Removal</div>
    <div class="front__name"><span class="first">DALE</span><span class="last">HOLLISTER</span><span class="rule"></span></div>
    <ul class="contact-list">
      <li><svg viewBox="0 0 10 10" aria-hidden="true"><path d="M2 0.5 L4 2.5 L3 3.8 Q4.5 6 6.2 7 L7.5 6 L9.5 8 L8 9.5 Q3 9 0.5 2 Z"/></svg>631-555-0148</li>
      <li><svg viewBox="0 0 10 10" aria-hidden="true"><rect x="0" y="1.5" width="10" height="7"/></svg>corvanepdr@mailbox-example.com</li>
      <li><svg viewBox="0 0 10 10" aria-hidden="true"><circle cx="5" cy="5" r="5"/></svg>corvanepdr.example</li>
    </ul>
    <div class="front__address">PO Box 518 Brookmere<br>NY 11962</div>
  </section>

  <section class="card card--back" aria-label="Business card back">
    <div class="back__top"></div>
    <p class="back__tagline">25 YEARS OF EXPERIENCE REMOVING DENTS<br>DINGS AND HAIL DAMAGE</p>
    <div class="back__brand">Corvane Paintless Dent Removal</div>
    <div class="back__channel"><span class="marker"></span>corvane paintless dent removal</div>
  </section>
</body>
</html>
```